Brookvane Consulting Business Card Design

Business Card Design for Brookvane Consulting. Brookvane Consulting is a boutique consultancy based in Atlanta, GA., that specializes in marketing strategy, organization planning, and leadership development. We provide solutions for small businesses and startups as well as Vantage 300 companies.

http://brookvaneconsulting.com/

Target Market(s)

We provide solutions for small businesses and startups as well as Vantage 300 companies.

Industry/Entity Type

Consulting

Contact Information for Business Card

Two sided business card with priority on contact information, logo, tag line (Guidance to Plan Boldly, Act Wisely, Grow Fully)

Colors

Designer to choose colors to be used in the design.

Requirements
Must have
• contact information, logo, tag line (Guidance to Plan Boldly, Act Wisely, Grow Fully)
• Simple no over communication.
Nice to have
• I would like to see different placements of logo and creative use of both sides of the card
Should not have
• Do not put too much information on the card.

```html
<!DOCTYPE html>
<html lang="en">
<head>
<meta charset="utf-8">
<title>Brookvane Consulting – Business Card</title>
<link href="https://fonts.googleapis.com/css2?family=Lato:wght@300;400;700&family=Satisfy&display=swap" rel="stylesheet">
<style>
  :root {
    --backdrop: #e9e7e4;
    --card-grey: #b9b9b9;
    --card-black: #151515;
    --mark-dark: #111111;
    --ink-light: #ffffff;
    --ink-soft: #f2f2f2;
  }
  html, body {
    margin: 0;
    padding: 0;
    width: 1200px;
    height: 769px;
    overflow: hidden;
    background: var(--backdrop);
  }
  .sheet {
    position: relative;
    width: 1200px;
    height: 769px;
    display: flex;
    align-items: center;
    justify-content: center;
    gap: 50px;
  }
  .card {
    position: relative;
    width: 520px;
    height: 300px;
    border-radius: 3px;
    overflow: hidden;
    box-shadow: 0 6px 18px rgba(0,0,0,0.18);
  }
  .card--contact { background: var(--card-grey); }
  .card--brand { background: var(--card-black); }
  .corner-block {
    position: absolute;
    left: 0;
    bottom: 0;
    width: 230px;
    height: 190px;
  }
  .person {
    position: absolute;
    top: 40px;
    right: 70px;
    text-align: center;
    color: var(--ink-light);
  }
  .person__name {
    font-family: "Satisfy", cursive;
    font-size: 30px;
    line-height: 1.1;
  }
  .person__role {
    font-family: "Lato", sans-serif;
    font-weight: 300;
    font-size: 14px;
    letter-spacing: 0.3px;
    color: var(--ink-soft);
  }
  .contact {
    position: absolute;
    right: 34px;
    top: 150px;
    text-align: right;
    font-family: "Lato", sans-serif;
    font-weight: 400;
    font-size: 14px;
    line-height: 1.35;
    color: var(--ink-light);
  }
  .brand {
    position: absolute;
    inset: 0;
    display: flex;
    flex-direction: column;
    align-items: center;
    justify-content: center;
    color: var(--ink-light);
    font-family: "Lato", sans-serif;
  }
  .brand__lockup {
    display: flex;
    align-items: center;
    gap: 12px;
  }
  .brand__dot {
    width: 16px;
    height: 16px;
    border-radius: 50%;
    background: var(--ink-light);
  }
  .brand__name {
    font-weight: 700;
    font-size: 34px;
    letter-spacing: 0.5px;
    white-space: nowrap;
  }
  .brand__tagline {
    margin-top: 34px;
    font-weight: 400;
    font-size: 14px;
    letter-spacing: 0.3px;
    white-space: nowrap;
  }
</style>
</head>
<body>
  <main class="sheet">
    <section class="card card--contact" aria-label="Business card, contact side">
      <svg class="corner-block" viewBox="0 0 230 190" role="img" aria-label="Dark corner panel where the large brand symbol belongs">
        <polygon points="0,0 230,0 40,190 0,190" fill="var(--mark-dark)"/>
      </svg>
      <div class="person">
        <div class="person__name">Dario Whitfield</div>
        <div class="person__role">Founder/Managing Director</div>
      </div>
      <div class="contact">
        <div>PHONE: 555-014-2290</div>
        <div>dario@brookvaneconsulting.com</div>
        <div>brookvaneconsulting.com</div>
      </div>
    </section>

    <section class="card card--brand" aria-label="Business card, brand side">
      <div class="brand">
        <div class="brand__lockup">
          <span class="brand__dot"></span>
          <span class="brand__name">Brookvane Consulting</span>
        </div>
        <div class="brand__tagline">Guidance to Plan Boldly, Act Wisely, Grow Fully</div>
      </div>
    </section>
  </main>
</body>
</html>
```